Dental Practice Billboard Design

We are a newer dental practice in need of a simple but appealing billboard for our growing dental practice to attract new patients. The practice is owned by husband and wife dentists and is family friendly in a small town in Kentucky. We try to be very friendly and caring to our patients. Would prefer a blue background for the billboard and our tooth logo to be prominent. We are partial to the Patua One font used in the image below but please feel free to tweak it as you deem necessary. The shape of the uppercase D and lowercase g are why we like that font, so fonts with a similarly shaped “D” and “g” would work as well. Please include our phone number (555) 847-1390. Please see our website Harlowbrookdentistry.example for more info on the practice if needed. Thank you! Looking forward to seeing your creation.
Updates

The dimensions will be 12ft x 24ft (3.6576m x 7.3152m). Apologies for not including this in the original prompt. Thank you all for your submissions.

Industry/Entity Type

Dental

Font styles to use
Other font styles liked:
• Patua One

Colors
0054AA
0677BA
7BADD7
CADEEF
E8F1F8
0094D4
00A9DD
6FCCEA
C7EBF8
E9F6FB
00AB8E
00BBA5
67D7C9
C6EFE9
E9F9F6
59FF00
82FF00
B8FF75
E3FFCB
F4FFEA

Requirements
Must have
• Phone number, website, Logo, Practice name “Harlow Brook Dentistry”
Should not have
• A tagline or slogan

```html
<!DOCTYPE html>
<html lang="en">
<head>
<meta charset="UTF-8">
<title>Harlow Brook Dentistry Billboard</title>
<link href="https://fonts.googleapis.com/css2?family=Patua+One&family=Montserrat:wght@700&display=swap" rel="stylesheet">
<style>
  :root {
    --page-bg: #e8ecf0;
    --brand-blue: #0756b8;
    --brand-green: #1fa824;
    --strip-white: #f4f9fc;
    --ink: #101418;
    --white: #ffffff;
    --photo-light: #f1f3f5;
    --photo-mid: #dde2e7;
    --photo-warm: #c9a48c;
  }
  * { box-sizing: border-box; margin: 0; padding: 0; }
  html, body {
    width: 1200px;
    height: 835px;
    overflow: hidden;
    background: var(--page-bg);
  }
  .billboard {
    position: absolute;
    left: 40px;
    top: 137px;
    width: 1120px;
    height: 560px;
    overflow: hidden;
    box-shadow: 0 10px 30px rgba(0, 0, 0, 0.18);
  }
  .billboard-shapes {
    position: absolute;
    inset: 0;
    width: 1120px;
    height: 560px;
  }
  .family-photo {
    position: absolute;
    inset: 0;
    clip-path: path("M 822 0 L 1120 0 L 1120 560 L 762 560 C 766 330 782 140 822 0 Z");
    background:
      radial-gradient(ellipse 150px 170px at 940px 250px, rgba(201, 164, 140, 0.6), transparent 70%),
      radial-gradient(ellipse 260px 160px at 950px 500px, var(--photo-mid), transparent 75%),
      linear-gradient(160deg, var(--photo-light), var(--photo-mid));
  }
  .brand-name {
    position: absolute;
    left: 0;
    top: 0;
    width: 740px;
    height: 455px;
    display: flex;
    align-items: center;
    justify-content: center;
    gap: 26px;
    font-family: "Patua One", serif;
    font-size: 84px;
    line-height: 1.05;
    color: var(--white);
  }
  .brand-dot {
    width: 44px;
    height: 44px;
    border-radius: 50%;
    background: var(--brand-green);
    flex: none;
  }
  .brand-text span { display: block; }
  .contact-strip {
    position: absolute;
    left: 22px;
    top: 486px;
    display: flex;
    align-items: center;
    gap: 22px;
    font-family: "Montserrat", sans-serif;
    font-weight: 700;
    color: var(--ink);
    white-space: nowrap;
  }
  .contact-item {
    display: flex;
    align-items: center;
    gap: 8px;
  }
  .contact-phone { font-size: 26px; }
  .contact-web { font-size: 22px; }
  .contact-icon { width: 24px; height: 24px; flex: none; }
</style>
</head>
<body>
  <div class="billboard">
    <svg class="billboard-shapes" viewBox="0 0 1120 560" aria-hidden="true">
      <rect class="panel-blue" x="0" y="0" width="1120" height="560" fill="var(--brand-blue)"/>
      <rect class="contact-band" x="0" y="455" width="800" height="105" fill="var(--strip-white)"/>
      <path class="accent-curve" d="M 798 0 L 822 0 C 782 140 766 330 762 560 L 734 560 C 738 330 756 140 798 0 Z" fill="var(--brand-green)"/>
    </svg>

    <div class="family-photo" role="img" aria-label="Photo of a smiling family of three in white shirts: a father, mother and young child"></div>

    <div class="brand-name">
      <span class="brand-dot"></span>
      <div class="brand-text">
        <span>Harlow Brook</span>
        <span>Dentistry</span>
      </div>
    </div>

    <div class="contact-strip">
      <div class="contact-item contact-phone">
        <svg class="contact-icon" viewBox="0 0 24 24" aria-hidden="true">
          <path d="M6.6 10.8a15.1 15.1 0 0 0 6.6 6.6l2.2-2.2a1 1 0 0 1 1-.25 11.4 11.4 0 0 0 3.6.57 1 1 0 0 1 1 1V20a1 1 0 0 1-1 1A17 17 0 0 1 3 4a1 1 0 0 1 1-1h3.5a1 1 0 0 1 1 1c0 1.25.2 2.45.57 3.57a1 1 0 0 1-.25 1z" fill="var(--brand-green)"/>
          <path d="M14 3.5a7 7 0 0 1 6.5 6.5M14 7a3.5 3.5 0 0 1 3 3" stroke="var(--brand-green)" stroke-width="1.8" fill="none" stroke-linecap="round"/>
        </svg>
        <span>(555) 847-1390</span>
      </div>
      <div class="contact-item contact-web">
        <svg class="contact-icon" viewBox="0 0 24 24" aria-hidden="true">
          <g fill="none" stroke="var(--brand-green)" stroke-width="1.8">
            <circle cx="12" cy="12" r="9.5"/>
            <ellipse cx="12" cy="12" rx="4.2" ry="9.5"/>
            <path d="M2.5 12h19M4 7h16M4 17h16"/>
          </g>
        </svg>
        <span>Harlowbrookdentistry.example</span>
      </div>
    </div>
  </div>
</body>
</html>
```